I need a sophisticated and powerful book cover design that combines Japanese minimalism with contemporary appeal. The cover should convey personal transformation through the metaphor of a katana (Japanese sword).
Key Design Elements:
A katana, either partially shown or artistically rendered
Subtle Japanese design elements without being stereotypical
Clean, minimalist aesthetic
Professional font selection that bridges Eastern and Western typography
Color scheme: Deep blacks, steel grays, and possibly a touch of red or gold for accent
Mood/Style:
Professional and sophisticated
Blend of traditional Japanese aesthetics with modern design
Should appeal to personal development and business readers
Must convey strength and transformation
Elegant rather than aggressive
Specific Requirements:
Title: "The Lantern Compass"
Subtitle: "Quiet Methods for Growing Inner Steadiness and Calm Endurance"
Author names: Dorvelan Thaske and Meloda Thaske
Cover dimensions: Standard hardcover book size (6" x 9")
Must work well in both physical and digital thumbnail formats
Should be striking and legible when viewed as a small image online
Design Specifics:
Japanese elements such as brushstroke effects, kanji characters, or wave patterns
The design should reflect the book's core message: personal transformation through Japanese wisdom principles, using the katana as a metaphor for growth and development.

```html
<!DOCTYPE html>
<html lang="en">
<head>
<meta charset="utf-8">
<title>The Lantern Compass — Book Cover</title>
<link rel="stylesheet" href="https://fonts.googleapis.com/css2?family=Montserrat:wght@400;500;600;900&family=Shojumaru&display=swap">
<style>
  :root {
    --stage: #000000;
    --paper: #ffffff;
    --ink: #111111;
    --accent-red: #ed1c24;
    --sun-red: #ee3b32;
    --steel-light: #e6e8ee;
    --steel-dark: #8a8f9c;
    --blossom: #f6b7c8;
    --blossom-soft: #fde6ee;
  }
  html, body {
    margin: 0;
    padding: 0;
    width: 1200px;
    height: 1200px;
    overflow: hidden;
    background: var(--stage);
  }
  .cover {
    position: absolute;
    left: 240px;
    top: 60px;
    width: 720px;
    height: 1080px;
    background: var(--paper);
    overflow: hidden;
    font-family: "Montserrat", sans-serif;
  }
  .artwork {
    position: absolute;
    left: 0;
    top: 0;
    width: 720px;
    height: 900px;
  }
  .title {
    margin: 0;
    font-size: inherit;
  }
  .title-the {
    position: absolute;
    left: 0;
    width: 720px;
    top: 544px;
    text-align: center;
    font-family: "Montserrat", sans-serif;
    font-weight: 900;
    font-size: 80px;
    letter-spacing: 6px;
    line-height: 1;
    color: var(--ink);
  }
  .title-lead {
    position: absolute;
    left: 0;
    width: 720px;
    top: 618px;
    text-align: center;
    font-family: "Shojumaru", cursive;
    font-size: 92px;
    line-height: 1.1;
    color: var(--accent-red);
  }
  .title-main {
    position: absolute;
    left: 0;
    width: 720px;
    top: 722px;
    text-align: center;
    font-family: "Montserrat", sans-serif;
    font-weight: 600;
    font-size: 112px;
    letter-spacing: 2px;
    line-height: 1;
    color: var(--accent-red);
  }
  .subtitle {
    position: absolute;
    left: 100px;
    width: 520px;
    top: 846px;
    margin: 0;
    text-align: center;
    font-weight: 500;
    font-size: 25px;
    line-height: 34px;
    letter-spacing: 0.6px;
    color: var(--ink);
  }
  .author-band {
    position: absolute;
    left: 0;
    bottom: 0;
    width: 720px;
    height: 115px;
    background: var(--accent-red);
    display: flex;
    align-items: center;
    justify-content: center;
  }
  .authors {
    margin: 0;
    font-weight: 400;
    font-size: 36px;
    letter-spacing: 0.5px;
    color: var(--paper);
  }
</style>
</head>
<body>
  <main class="cover">
    <svg class="artwork" viewBox="0 0 720 900" xmlns="http://www.w3.org/2000/svg">
      <defs>
        <linearGradient id="blade-tone" x1="0" y1="0" x2="1" y2="0">
          <stop offset="0" stop-color="#8a8f9c"/>
          <stop offset="0.5" stop-color="#e6e8ee"/>
          <stop offset="1" stop-color="#8a8f9c"/>
        </linearGradient>
        <radialGradient id="blossom-tone" cx="0.45" cy="0.35" r="0.55">
          <stop offset="0" stop-color="#f6b7c8"/>
          <stop offset="1" stop-color="#fde6ee" stop-opacity="0"/>
        </radialGradient>
      </defs>
      <circle class="sun-disc" cx="372" cy="344" r="255" fill="#ee3b32"
              role="img" aria-label="Red watercolour brush-painted sun disc"/>
      <ellipse class="blossom-branch" cx="170" cy="110" rx="170" ry="150" fill="url(#blossom-tone)"
            role="img" aria-label="Branch of pink cherry blossoms reaching in from the top left"/>
      <rect class="sword" x="344" y="8" width="37" height="815" rx="4" fill="url(#blade-tone)"
            role="img" aria-label="Upright katana with black wrapped hilt, gold guard and steel blade"/>
    </svg>

    <h1 class="title">
      <span class="title-the">THE</span>
      <span class="title-lead">LANTERN</span>
      <span class="title-main">COMPASS</span>
    </h1>

    <p class="subtitle">Quiet Methods for Growing Inner Steadiness and Calm Endurance</p>

    <footer class="author-band">
      <p class="authors">Dorvelan Thaske &amp; Meloda Thaske</p>
    </footer>
  </main>
</body>
</html>
```